Website for Reiki and Wellness Courses

I teach online courses in Reiki and wellness/self-development and am needing a new website.

The focus of the website will be to provide descriptions of the courses as well as include a blog and pages where students in my courses will visit for additional information.

Note: courses are NOT hosted on this site.
The focus of this website will be to encourage viewers to enroll in courses as well as opt in to the email list.

I will upload copy soon. My old website is: http://brightfernstudies.example. Please do not use existing logo.

Target Market(s)

Alternative health, wellness, spirituality, personal development. Males and females of all ages seeking to improve their health and life.

Industry/Entity Type

Health And Wellness

Logo Text

No text (please do not use existing logo)

Coding

Coded - Design and coding required

Number of Pages Required

5+ page

Requirements
Must have
• 1. Home page
• 2. About page
• 3. Courses page that outlines courses (there are currently 6 courses with 1 coming soon)
• 4. Individual course page (maybe a template that I can adjust color and pictures for with each course)
• 5. Blog
• 6. Student Area that outlines all Student Areas
• 7. Individual Student Area page (maybe a template that I can adjust color and pictures for with each course)
• 8. Shop page (note: items will not currently be purchased through website - it will be a link to quillmarket for a book).
• 9. Student thank-you page (maybe a template that I can adjust color and pictures for with each course) this is the page students are directed to at end of course with vouchers for other courses.
• Opt-in for the home page, course pages, blog and thank-you pages
Nice to have
• I would like the design to be calm, clean and soothing. Ideally visitors feel relaxed when viewing the site and are encouraged to explore the courses, subscribe to the email list and purchase a product.
• ~ Testimonials page
• ~ Contact page
• I tend to gravitate towards blues, greys and purples as well as monochromatic color schemes.
Should not have
• Contact form on home page
• phone number on home page
• location/physical address
• dates for blog posts

```html
<!DOCTYPE html>
<html lang="en">
<head>
<meta charset="utf-8">
<title>Bright Fern Studies — Reiki &amp; Wellness Courses</title>
<link href="https://fonts.googleapis.com/css2?family=Raleway:wght@400;500;600;700&family=Open+Sans:ital,wght@0,400;0,600;0,700;1,700&display=swap" rel="stylesheet">
<style>
:root{
  --purple:#a23fc6;
  --purple-dark:#7d2ea1;
  --pink:#e8308a;
  --blue:#1f4c9e;
  --navy:#2b3f68;
  --teal:#129c8e;
  --teal-light:#4ec6b6;
  --green:#3fa652;
  --orange:#ef7d2a;
  --ink:#333a44;
  --muted:#6b7280;
  --grey-bg:#f1f2f4;
  --footer:#525a6e;
  --footer-dark:#3b4152;
  --white:#ffffff;
}
*{box-sizing:border-box;margin:0;padding:0}
html,body{width:1200px;height:3732px;overflow:hidden}
body{font-family:"Open Sans",Arial,sans-serif;color:var(--ink);font-size:13px;line-height:1.6;background:var(--white)}
h1,h2,h3,h4{font-family:"Raleway",Arial,sans-serif}
.wrap{width:1000px;margin:0 auto;position:relative}
.btn{display:inline-block;color:var(--white);font-family:"Raleway",Arial,sans-serif;font-weight:600;font-size:14px;letter-spacing:.5px;padding:12px 26px;text-transform:uppercase;text-decoration:none}
.btn-blue{background:var(--blue)}
.btn-pink{background:var(--pink)}
.btn-purple{background:var(--purple)}
.section-title{text-align:center;font-weight:500;font-size:38px;letter-spacing:1px;text-transform:uppercase}

/* hero */
.hero{height:660px;position:relative;background:linear-gradient(180deg,#8fb2cf 0%,#c9d5e2 40%,#e6dcd4 70%,#b7c6d8 100%);overflow:hidden}
.hero-photo{position:absolute;right:120px;top:80px;width:460px;height:580px;border-radius:50% 50% 0 0;background:radial-gradient(ellipse at 50% 30%,rgba(255,255,255,.85) 0%,rgba(230,225,220,.55) 35%,rgba(180,170,165,.35) 65%,rgba(255,255,255,0) 80%)}
.nav{position:absolute;top:16px;left:100px;right:100px;display:flex;align-items:center;justify-content:space-between}
.brand{display:flex;align-items:center;gap:10px;color:var(--white);font-family:"Raleway",Arial,sans-serif;font-weight:700;font-size:18px;letter-spacing:1px}
.brand-dot{width:34px;height:34px;border-radius:50%;background:var(--purple)}
.menu{display:flex;gap:6px;list-style:none}
.menu a{display:block;color:var(--white);text-decoration:none;font-family:"Raleway",Arial,sans-serif;font-weight:600;font-size:14px;padding:10px 14px}
.menu .active a{background:var(--purple)}
.hero-copy{position:absolute;left:100px;top:228px;width:480px}
.hero-copy h1{color:var(--purple);font-weight:500;font-size:50px;line-height:1.15}
.hero-copy p{font-weight:700;font-style:italic;font-size:16px;color:#111;margin:22px 0 30px;line-height:1.45}

/* welcome */
.welcome{height:540px;padding-top:68px}
.welcome .eyebrow{font-family:"Raleway",Arial,sans-serif;font-size:14px;text-transform:uppercase;color:var(--ink)}
.welcome h2{color:var(--purple);font-weight:700;font-size:34px;margin:2px 0 18px;text-transform:uppercase}
.welcome-text{width:600px}
.welcome-text p{font-size:13px;color:var(--muted);margin-bottom:14px}
.welcome-photo{position:absolute;right:0;top:20px;width:330px;height:250px;background:linear-gradient(135deg,#d8c3b1,#efe3d8 55%,#c9b4a6)}
.play{position:absolute;left:50%;top:50%;width:54px;height:54px;margin:-27px 0 0 -27px}

/* courses */
.courses{height:520px;background:linear-gradient(180deg,#a65fd0 0%,#c2a3e1 30%,#d9e4f3 70%,#eef2fa 100%);padding-top:48px}
.courses .section-title{color:var(--navy)}
.course-grid{display:flex;gap:20px;margin-top:28px}
.course-card{width:235px;background:var(--white);text-align:center;position:relative;padding-bottom:18px}
.course-img{height:170px}
.course-icon{width:40px;height:40px;border-radius:50%;background:var(--purple);border:4px solid var(--white);margin:-20px auto 4px;position:relative}
.course-card h3{font-family:"Open Sans",Arial,sans-serif;font-size:11px;font-weight:600;text-transform:uppercase;line-height:1.4;height:32px;padding:0 18px}
.course-card .btn{font-size:13px;padding:8px 22px;margin-top:8px}
.c-blue h3{color:var(--blue)} .c-blue .btn{background:var(--blue)}
.c-green h3{color:var(--green)} .c-green .btn{background:var(--green)}
.c-orange h3{color:var(--orange)} .c-orange .btn{background:var(--orange)}
.c-pink h3{color:var(--pink)} .c-pink .btn{background:var(--pink)}
.view-all{text-align:center;margin-top:26px}

/* student areas */
.students{height:420px;padding-top:52px;position:relative}
.students h2{color:var(--navy);font-weight:500;font-size:38px;text-transform:uppercase;margin-left:60px}
.student-list{list-style:none;margin:20px 0 0 60px}
.student-list li{display:flex;align-items:center;gap:10px;font-size:13px;color:var(--ink);margin-bottom:7px}
.student-list li:first-child{font-weight:700}
.student-list svg{flex:none}
.students-photo{position:absolute;right:130px;top:20px;width:280px;height:380px;border-radius:140px 140px 0 0;background:linear-gradient(180deg,#f4f4f4,#e5e2df 50%,#f7f6f5)}

/* blog */
.blog{height:580px;background:linear-gradient(160deg,var(--teal-light) 0%,var(--teal) 50%,#0d7f75 100%);padding-top:46px}
.blog .section-title{color:var(--white)}
.blog-grid{display:flex;gap:20px;margin-top:30px}
.post{width:235px;background:var(--white);padding-bottom:16px}
.post-img{height:180px}
.post h3{font-family:"Open Sans",Arial,sans-serif;font-weight:600;font-size:14px;color:var(--blue);padding:14px 14px 6px;line-height:1.35}
.post p{font-size:12px;color:var(--muted);padding:0 14px;line-height:1.5}
.post a{display:block;padding:8px 14px 0;font-size:11px;font-weight:700;color:var(--ink);text-decoration:none}

/* testimonials */
.clients{height:460px;background:var(--grey-bg);padding-top:52px;text-align:center;position:relative}
.clients .section-title{color:var(--navy)}
.quote-badge{width:72px;height:72px;margin:26px auto 22px}
.quote{width:780px;margin:0 auto;font-size:13px;color:var(--muted);line-height:1.7}
.quote-author{color:var(--green);font-weight:600;margin-top:18px;font-size:14px}
.arrow{position:absolute;top:210px;width:36px;height:36px}
.arrow-left{left:90px} .arrow-right{right:90px}

/* opt-in */
.optin{height:300px;padding-top:60px;text-align:center}
.optin h2{color:var(--navy);font-weight:500;font-size:38px;text-transform:uppercase;letter-spacing:1px}
.optin p{font-size:13px;color:var(--muted);margin:10px 0 26px}
.optin-form{display:flex;gap:22px;justify-content:center;align-items:center}
.field{width:208px;height:40px;border:1px solid #c9ccd3;font-size:12px;color:#8a8f99;text-align:left;padding:10px 12px;font-family:"Open Sans",Arial,sans-serif}
.optin .btn{padding:11px 22px;font-size:15px}

/* footer */
.footer{height:200px;background:var(--footer);color:#e3e6ee;padding-top:26px}
.footer .wrap{display:flex;justify-content:space-between}
.fcol h4{font-family:"Raleway",Arial,sans-serif;font-size:14px;font-weight:700;color:var(--white);text-transform:uppercase;margin-bottom:12px}
.fcol ul{list-style:none;font-size:12px;line-height:1.7}
.contact-line{display:flex;gap:8px;align-items:flex-start;font-size:12px;margin-bottom:8px}
.contact-line strong{color:var(--white)}
.newsletter p{font-size:12px;width:220px;line-height:1.5}
.news-field{width:220px;height:28px;background:var(--white);margin:10px 0}
.news-btn{border:1px solid #d6d9e0;color:var(--white);font-size:12px;padding:5px 14px;display:inline-block;font-weight:600}
.social{display:flex;align-items:center;gap:10px;font-size:12px;margin-bottom:10px}
.social span.dot{width:28px;height:28px;border-radius:50%;background:#6c7489;display:block}
.bottom-bar{height:52px;background:var(--footer-dark);color:#d2d6df;font-size:12px;text-align:center;line-height:52px}
.bottom-bar strong{color:var(--white)}
</style>
</head>
<body>

<header class="hero">
  <div class="hero-photo" role="img" aria-label="Photo of a woman meditating cross-legged against a glowing sky"></div>
  <nav class="nav">
    <div class="brand"><span class="brand-dot"></span>BRIGHT FERN STUDIES</div>
    <ul class="menu">
      <li class="active"><a href="#">HOME</a></li>
      <li><a href="#">ABOUT</a></li>
      <li><a href="#">COURSES</a></li>
      <li><a href="#">BLOG</a></li>
      <li><a href="#">STUDENT AREA</a></li>
      <li><a href="#">CONTACT</a></li>
    </ul>
  </nav>
  <div class="hero-copy">
    <h1>Become a Certified USUI Reiki Master</h1>
    <p>This comprehensive online course gives you all of the tools you need to be certified as a Traditional Usui Reiki Master.</p>
    <a class="btn btn-blue" href="#">Know More</a>
  </div>
</header>

<section class="welcome">
  <div class="wrap">
    <div class="welcome-text">
      <div class="eyebrow">Welcome to</div>
      <h2>Bright Fern Studies</h2>
      <p>Thought to be centuries old and rediscovered in the late 1800s, Reiki (pronounced ray-kee) is a healing and enlightenment system. The word Reiki can be translated into "Universal Life Energy." As a practitioner of Reiki, you attune your awareness to this energy and utilize it for the physical and emotional healing of self and others.</p>
      <p>Reiki is non-denominational and can be practiced by everyone, regardless of their religious and spiritual beliefs. Reiki can be performed hands-on in person or from a distance.</p>
      <a class="btn btn-pink" href="#">Know More</a>
    </div>
    <div class="welcome-photo" role="img" aria-label="Video still of hands giving a Reiki treatment">
      <svg class="play" viewBox="0 0 54 54"><circle cx="27" cy="27" r="26" fill="rgba(255,255,255,.85)"/><path d="M22 17 L38 27 L22 37 Z" fill="#7d2ea1"/></svg>
    </div>
  </div>
</section>

<section class="courses">
  <div class="wrap">
    <h2 class="section-title">Our Courses</h2>
    <div class="course-grid">
      <article class="course-card c-blue">
        <div class="course-img" role="img" aria-label="Photo of hands over a client's head" style="background:linear-gradient(135deg,#9ec3e6,#e2d6ca)"></div>
        <div class="course-icon"></div>
        <h3>Reiki Level I, II Master Certification</h3>
        <a class="btn" href="#">Read More</a>
      </article>
      <article class="course-card c-green">
        <div class="course-img" role="img" aria-label="Photo of a small white dog receiving healing" style="background:linear-gradient(135deg,#b9d7ee,#f2efe9)"></div>
        <div class="course-icon"></div>
        <h3>Animal Reiki Practitioner Certification</h3>
        <a class="btn" href="#">Read More</a>
      </article>
      <article class="course-card c-orange">
        <div class="course-img" role="img" aria-label="Photo of stacked stones on sand" style="background:linear-gradient(135deg,#e8e2da,#b9b2a8)"></div>
        <div class="course-icon"></div>
        <h3>Crystal Reiki Practitioner Certification</h3>
        <a class="btn" href="#">Read More</a>
      </article>
      <article class="course-card c-pink">
        <div class="course-img" role="img" aria-label="Photo of a person meditating by the sea" style="background:linear-gradient(180deg,#9cc7e3,#e9d9c4)"></div>
        <div class="course-icon"></div>
        <h3>Your Soul Is Calling</h3>
        <a class="btn" href="#">Read More</a>
      </article>
    </div>
    <div class="view-all"><a class="btn btn-purple" href="#">View All</a></div>
  </div>
</section>

<section class="students">
  <div class="wrap">
    <h2>Student Areas</h2>
    <ul class="student-list">
      <li><svg width="12" height="12" viewBox="0 0 12 12"><path d="M3 1 L9 6 L3 11" fill="none" stroke="#a23fc6" stroke-width="2"/></svg>Reiki Level I, II Master Certification</li>
      <li><svg width="12" height="12" viewBox="0 0 12 12"><path d="M3 1 L9 6 L3 11" fill="none" stroke="#a23fc6" stroke-width="2"/></svg>Animal Reiki Practitioner Certification</li>
      <li><svg width="12" height="12" viewBox="0 0 12 12"><path d="M3 1 L9 6 L3 11" fill="none" stroke="#a23fc6" stroke-width="2"/></svg>Crystal Reiki Practitioner Certification</li>
      <li><svg width="12" height="12" viewBox="0 0 12 12"><path d="M3 1 L9 6 L3 11" fill="none" stroke="#a23fc6" stroke-width="2"/></svg>Build Your Reiki Business</li>
      <li><svg width="12" height="12" viewBox="0 0 12 12"><path d="M3 1 L9 6 L3 11" fill="none" stroke="#a23fc6" stroke-width="2"/></svg>Acupressure and Reiki for Anxiety and Depression</li>
      <li><svg width="12" height="12" viewBox="0 0 12 12"><path d="M3 1 L9 6 L3 11" fill="none" stroke="#a23fc6" stroke-width="2"/></svg>Your Soul is Calling</li>
      <li><svg width="12" height="12" viewBox="0 0 12 12"><path d="M3 1 L9 6 L3 11" fill="none" stroke="#a23fc6" stroke-width="2"/></svg>Sacred Sound and Breath</li>
    </ul>
    <div class="students-photo" role="img" aria-label="Photo of a woman in white sitting in meditation"></div>
  </div>
</section>

<section class="blog">
  <div class="wrap">
    <h2 class="section-title">Latest Blog</h2>
    <div class="blog-grid">
      <article class="post">
        <div class="post-img" role="img" aria-label="Photo of pebbles stacked on sand" style="background:linear-gradient(135deg,#d9d2c7,#a79f93)"></div>
        <h3>Using Your Reiki Box to Manifest Goals</h3>
        <p>We have entered a new year &amp; with that inevitably comes the desire to start fresh.</p>
        <a href="#">READ MORE...»</a>
      </article>
      <article class="post">
        <div class="post-img" role="img" aria-label="Photo of a prayer bead bracelet on wood" style="background:linear-gradient(135deg,#6b4a3a,#b38a6a)"></div>
        <h3>Why Reiki Does Not Prescribe Or Diagnose</h3>
        <p>We have entered a new year &amp; with that inevitably comes the desire to start fresh.</p>
        <a href="#">READ MORE...»</a>
      </article>
      <article class="post">
        <div class="post-img" role="img" aria-label="Photo of balanced stones in calm water" style="background:linear-gradient(135deg,#c9dbe6,#8ea9b8)"></div>
        <h3>Using Your Reiki Box to Manifest Goals</h3>
        <p>We have entered a new year &amp; with that inevitably comes the desire to start fresh.</p>
        <a href="#">READ MORE...»</a>
      </article>
      <article class="post">
        <div class="post-img" role="img" aria-label="Photo of a raked sand garden" style="background:linear-gradient(135deg,#eee8df,#cfc5b7)"></div>
        <h3>Why Reiki Does Not Prescribe Or Diagnose</h3>
        <p>We have entered a new year &amp; with that inevitably comes the desire to start fresh.</p>
        <a href="#">READ MORE...»</a>
      </article>
    </div>
  </div>
</section>

<section class="clients">
  <h2 class="section-title">What Our Client Say</h2>
  <svg class="quote-badge" viewBox="0 0 72 72"><circle cx="36" cy="36" r="34" fill="none" stroke="#129c8e" stroke-width="3"/><path d="M24 40 q0-10 8-14 v4 q-4 2-4 6 h4 v8 h-8z M38 40 q0-10 8-14 v4 q-4 2-4 6 h4 v8 h-8z" fill="#129c8e"/></svg>
  <p class="quote">" I was drawn to this course with the desire to heal family, friends and pets and this course has given me that ability and so much more. With it, Reiki has healed me on many levels and given me insight into my own spirituality and to what is possible. The continued contact with Mara Linden on the community group as well as input and questions are answered from other. "</p>
  <p class="quote-author">— Dana Whitlow</p>
  <svg class="arrow arrow-left" viewBox="0 0 36 36"><circle cx="18" cy="18" r="17" fill="#dfe1e5"/><path d="M21 11 L14 18 L21 25" fill="none" stroke="#fff" stroke-width="2.5"/></svg>
  <svg class="arrow arrow-right" viewBox="0 0 36 36"><circle cx="18" cy="18" r="17" fill="#dfe1e5"/><path d="M15 11 L22 18 L15 25" fill="none" stroke="#fff" stroke-width="2.5"/></svg>
</section>

<section class="optin">
  <h2>Stay Inspired</h2>
  <p>Receive information and articles each month to keep you feeling inspired. As a thank you, you will also receive access to soothing music<br>you can download for use in your Reiki sessions and meditation.</p>
  <div class="optin-form">
    <div class="field">First Name*</div>
    <div class="field">Last Name*</div>
    <div class="field">Email Id*</div>
    <a class="btn btn-pink" href="#">Yes-Count Me In</a>
  </div>
</section>

<footer class="footer">
  <div class="wrap">
    <div class="fcol">
      <h4>Sitemap</h4>
      <ul><li>Home</li><li>About Us</li><li>Courses</li><li>Blog</li><li>Student areas</li><li>Contact</li></ul>
    </div>
    <div class="fcol">
      <h4>Get in Touch</h4>
      <div class="contact-line"><svg width="12" height="14" viewBox="0 0 12 14"><path d="M6 0a5 5 0 0 1 5 5c0 4-5 9-5 9S1 9 1 5a5 5 0 0 1 5-5z" fill="#e3e6ee"/><circle cx="6" cy="5" r="2" fill="#525a6e"/></svg><span><strong>BRIGHT FERN STUDIES</strong><br>Gentle lessons for a calmer<br>mind, body and spirit.</span></div>
      <div class="contact-line"><svg width="12" height="12" viewBox="0 0 12 12"><path d="M2 1h3l1 3-2 1a7 7 0 0 0 3 3l1-2 3 1v3a1 1 0 0 1-1 1A10 10 0 0 1 1 2a1 1 0 0 1 1-1z" fill="#e3e6ee"/></svg>+1 (555) 014 2290</div>
      <div class="contact-line"><svg width="12" height="10" viewBox="0 0 12 10"><rect x="0.5" y="0.5" width="11" height="9" fill="none" stroke="#e3e6ee"/><path d="M0.5 0.5 L6 5 L11.5 0.5" fill="none" stroke="#e3e6ee"/></svg>hello@brightfernstudies.example</div>
    </div>
    <div class="fcol newsletter">
      <h4>Newsletter</h4>
      <p>Would you like to receive occasional quotes or articles, soothing tracks and course news sent to your inbox?</p>
      <div class="news-field"></div>
      <span class="news-btn">SUBSCRIBE</span>
    </div>
    <div class="fcol">
      <h4>Follow Us</h4>
      <div class="social"><span class="dot"></span>Community</div>
      <div class="social"><span class="dot"></span>Updates</div>
      <div class="social"><span class="dot"></span>News</div>
    </div>
  </div>
</footer>
<div class="bottom-bar"><strong>BRIGHT FERN STUDIES</strong> · 2016 All rights reserved</div>

</body>
</html>
```